Bry7Legal Letterhead

Need a new letterhead for my law firm.
IDENTIFYING INFORMATION BELOW:
Anselmo R Quintara III
Attorney at Law
Address: 2847 Larkspur Blvd, Ste 300, Dallas, TX 75204
Phone: 877-482-6017
Fax: 469-738-1452
Email: bry@bry7legal.example
Website: www.bry7legal.example

Colors
0054AA
0677BA
7BADD7
CADEEF
E8F1F8

Requirements
Must have
• Logo needs to be on the letterhead, along with identifying information which is included in the project description.

```html
<!DOCTYPE html>
<html lang="en">
<head>
<meta charset="utf-8">
<title>Bry7Legal Letterhead</title>
<link href="https://fonts.googleapis.com/css2?family=Open+Sans:wght@400;700&display=swap" rel="stylesheet">
<style>
  :root {
    --backdrop: #d9dddf;
    --paper: #ffffff;
    --ink: #0b0b0b;
    --accent: #0677ba;
    --on-dark: #ffffff;
  }
  * { box-sizing: border-box; margin: 0; padding: 0; }
  html, body { width: 1200px; height: 784px; overflow: hidden; }
  body {
    background: var(--backdrop);
    font-family: "Open Sans", Arial, sans-serif;
    color: var(--ink);
    position: relative;
  }
  .letterhead {
    position: absolute;
    left: 314px; top: 22px;
    width: 572px; height: 740px;
    background: var(--paper);
    box-shadow: 0 2px 8px rgba(0,0,0,.12);
  }
  .corner-square {
    position: absolute;
    width: 46px; height: 46px;
    background: var(--accent);
  }
  .corner-square--top { left: 0; top: 0; }
  .corner-square--bottom { right: 0; bottom: 0; }

  .brand {
    position: absolute;
    left: 56px; top: 12px;
  }
  .brand__name {
    font-weight: 700;
    font-size: 24px;
    line-height: 1.1;
    color: var(--ink);
  }
  .brand__tagline {
    font-weight: 400;
    font-size: 9px;
    line-height: 1.2;
    margin-top: 2px;
    color: var(--ink);
  }

  .band {
    position: absolute;
    background: var(--ink);
    color: var(--on-dark);
  }
  .band--top {
    left: 212px; right: 0; top: 52px; height: 38px;
    text-align: right;
    padding: 7px 12px 0 0;
  }
  .attorney__name { font-weight: 700; font-size: 9.5px; letter-spacing: .3px; line-height: 13px; text-transform: uppercase; }
  .attorney__title { font-size: 7px; letter-spacing: .8px; line-height: 10px; margin-top: 1px; text-transform: uppercase; }

  .band--bottom {
    left: 0; width: 238px; bottom: 60px; height: 42px;
    text-align: right;
    padding: 8px 8px 0 0;
    font-size: 8px;
    line-height: 13px;
    white-space: nowrap;
  }
  .contact__item { display: inline-flex; align-items: center; gap: 3px; margin-left: 6px; }
  .contact__item svg { width: 8px; height: 8px; fill: var(--on-dark); }

  .address {
    position: absolute;
    left: 246px; bottom: 66px;
    font-style: normal;
    font-weight: 700;
    font-size: 10px;
    line-height: 13px;
    white-space: nowrap;
  }
</style>
</head>
<body>
  <main class="letterhead">
    <div class="corner-square corner-square--top"></div>

    <header class="brand">
      <div class="brand__name">Bry7Legal</div>
      <div class="brand__tagline">Trusted counsel in Dallas</div>
    </header>

    <div class="band band--top">
      <div class="attorney__name">Anselmo R Quintara III</div>
      <div class="attorney__title">Attorney at Law</div>
    </div>

    <footer class="band band--bottom">
      <div class="contact__row">
        <span class="contact__item">877-482-6017
          <svg viewBox="0 0 10 10"><path d="M2 1l2 2-1 1.2c.6 1.2 1.6 2.2 2.8 2.8L7 6l2 2-1.3 1.3C4.5 9 1 5.5.7 2.3z"/></svg>
        </span>
        <span class="contact__item">469-738-1452
          <svg viewBox="0 0 10 10"><path d="M2 0h5v3H2zM0 3.5h10V9H0z"/></svg>
        </span>
      </div>
      <div class="contact__row">
        <span class="contact__item">bry@bry7legal.example
          <svg viewBox="0 0 10 10"><path d="M0 2h10v6H0z"/></svg>
        </span>
        <span class="contact__item">www.bry7legal.example
          <svg viewBox="0 0 10 10"><circle cx="5" cy="5" r="4.5"/></svg>
        </span>
      </div>
    </footer>

    <address class="address">
      2847 Larkspur Blvd, Ste 300,<br>Dallas, TX 75204
    </address>

    <div class="corner-square corner-square--bottom"></div>
  </main>
</body>
</html>
```